indépendant en tant que Massothérapeute et Préparateur Mental, j'ai besoin de ...

Massothérapeute et préparateur mental indépendant, je recherche une carte de visite sobre et dynamique, sans images liées au massage ou à la préparation mentale mais intégrant mon logo. Les couleurs que j'aime bien sont : Blanc, gris, anthracite, noir et jaune

Contact Information for Business Card

carte de préférence Horizontale
neutre qui puisse toucher le deux domaines Massothérapie et préparation mentale

Requirements
Must have
• mon projet doit intégrer au recto:
LOGO
Loïc Bardèze
078 513 26 48
info@loicbardeze.ch
et éventuellement www.loicbardeze.ch

et au verso les deux adresses:

Chemin des Ormilles 7B
1400 Yverdon-les-Bains

Route de la Gravière 9
1700 Fribourg

Should not have
• mon projet ne doit pas contenir d'image en liens avec le massage ni la préparation mentale.

```html
<!DOCTYPE html>
<html lang="fr">
<head>
<meta charset="utf-8">
<title>Loïc Bardèze — Carte de visite</title>
<link rel="stylesheet" href="https://fonts.googleapis.com/css2?family=Lato:wght@400;700&display=swap">
<style>
  :root {
    --backdrop: #e4e4e4;
    --anthracite: #2e2e2e;
    --ink: #111111;
    --white: #ffffff;
    --panel-grey: #e6e5e3;
    --muted-line: #8a8a8a;
    --accent-yellow: #f2b705;
  }
  * { margin: 0; padding: 0; box-sizing: border-box; }
  html, body {
    width: 1200px; height: 801px; overflow: hidden;
    background: var(--backdrop);
    font-family: "Lato", Arial, sans-serif;
  }
  .canvas { position: relative; width: 1200px; height: 801px; }

  .card { position: absolute; left: 354px; width: 517px; height: 310px; }

  /* Verso: dark side with addresses */
  .card--addresses { top: 45px; background: var(--anthracite); color: var(--white); }
  .brand-name {
    position: absolute; top: 154px; left: 0; width: 100%;
    text-align: center; font-weight: 700; font-size: 20px; letter-spacing: 1px;
    color: var(--white);
  }
  .addresses {
    position: absolute; top: 211px; left: 78px;
    display: flex; align-items: center; font-size: 11.5px; line-height: 16px; letter-spacing: .3px;
  }
  .addresses .pin { width: 14px; height: 19px; margin-right: 10px; }
  .addresses .divider { width: 14px; height: 28px; margin: 0 9px; }

  /* Recto: framed contact side */
  .card--contact { top: 423px; background: var(--white); padding: 17px; }
  .card--contact .panel { position: relative; width: 100%; height: 100%; background: var(--panel-grey); color: var(--ink); }
  .accent-tick { position: absolute; left: 0; bottom: 0; width: 18px; height: 2px; background: var(--accent-yellow); }
  .holder-name {
    position: absolute; left: 17px; top: 154px;
    font-weight: 700; font-size: 17px; letter-spacing: 1.4px; text-transform: uppercase;
  }
  .holder-rule { position: absolute; left: 19px; top: 180px; width: 12px; height: 1px; background: var(--ink); }
  .contact-list { position: absolute; left: 19px; top: 190px; list-style: none; font-size: 13px; line-height: 22px; letter-spacing: .3px; }
  .contact-list b { font-weight: 700; }
  .signature {
    position: absolute; right: 17px; bottom: 30px;
    display: flex; align-items: center; gap: 8px;
    font-weight: 700; font-size: 17px; letter-spacing: .5px;
  }
  .signature .mark { width: 12px; height: 12px; background: var(--ink); }
</style>
</head>
<body>
<main class="canvas">

  <section class="card card--addresses" aria-label="Verso : adresses">
    <div class="brand-name">Loïc Bardèze</div>
    <div class="addresses">
      <svg class="pin" viewBox="0 0 14 19" aria-hidden="true">
        <path d="M7 0C3.1 0 0 3.1 0 7c0 5 7 12 7 12s7-7 7-12C14 3.1 10.9 0 7 0zm0 9.6A2.6 2.6 0 1 1 7 4.4a2.6 2.6 0 0 1 0 5.2z" fill="#ffffff"/>
      </svg>
      <address class="address" style="font-style:normal">Chemin des Ormilles 7B<br>1400 Yverdon-les-Bains</address>
      <svg class="divider" viewBox="0 0 14 28" aria-hidden="true">
        <line x1="13" y1="1" x2="1" y2="27" stroke="#8a8a8a" stroke-width="1"/>
      </svg>
      <address class="address" style="font-style:normal">Route de la Gravière 9<br>1700 Fribourg</address>
    </div>
  </section>

  <section class="card card--contact" aria-label="Recto : coordonnées">
    <div class="panel">
      <h1 class="holder-name">Loïc Bardèze</h1>
      <div class="holder-rule"></div>
      <ul class="contact-list">
        <li><b>M</b> : 078 513 26 48</li>
        <li><b>E</b>&nbsp; : info@loicbardeze.ch</li>
        <li><b>W</b> : www.loicbardeze.ch</li>
      </ul>
      <div class="signature"><span class="mark"></span>Loïc Bardèze</div>
    </div>
    <span class="accent-tick"></span>
  </section>

</main>
</body>
</html>
```